We are a recruitment company based in Norwich/Cambridge England.
I have included our company logo which we want to remain the same.

What we are looking for is a new creative Business card which will really stand out!!

Contact Information for Business Card

Harriet Dunmore
email: Harriet@plavex.co.uk
Address: Brackwell House
Fenmoor Enterprise Park
Partridge Way
Norwich
QB9 3KX
Tel:01632 960418

```html
<!DOCTYPE html>
<html lang="en">
<head>
<meta charset="utf-8">
<title>Plavex Business Card</title>
<link rel="stylesheet" href="https://fonts.googleapis.com/css2?family=Work+Sans:wght@400;500;600&display=swap">
<style>
  :root {
    --backdrop: #161616;
    --card-light: #ffffff;
    --card-dark: #232323;
    --card-dark-glow: #3a3938;
    --brand-green: #7dc242;
    --text-grey: #4a4a4a;
    --mark-grey: #8a8a8a;
    --text-white: #ffffff;
  }
  * { margin: 0; padding: 0; box-sizing: border-box; }
  html, body { width: 1200px; height: 897px; overflow: hidden; background: var(--backdrop); }
  body { font-family: "Work Sans", Arial, sans-serif; }
  .canvas { position: relative; width: 1200px; height: 897px; background: var(--backdrop); }

  .card { position: absolute; left: 303px; width: 595px; height: 338px; border-radius: 24px; overflow: hidden; }
  .card--front { top: 92px; background: var(--card-light); }
  .card--back { top: 469px; background: radial-gradient(circle at 88% 70%, var(--card-dark-glow) 0%, var(--card-dark) 55%, #1c1c1c 100%); }

  .brand { position: absolute; display: flex; align-items: center; gap: 12px; font-weight: 600; letter-spacing: -0.5px; line-height: 1; }
  .brand__dot { border-radius: 50%; background: var(--brand-green); flex: none; }
  .card--front .brand { left: 41px; top: 142px; font-size: 44px; color: var(--mark-grey); }
  .card--front .brand__dot { width: 44px; height: 44px; }
  .card--back .brand { left: 50%; top: 140px; transform: translateX(-50%); font-size: 58px; color: var(--text-white); }
  .card--back .brand__dot { width: 58px; height: 58px; }

  .divider { position: absolute; left: 312px; top: 94px; width: 2px; height: 151px; background: var(--brand-green); }

  .contact { position: absolute; left: 343px; top: 92px; color: var(--text-grey); }
  .contact__name { font-size: 24px; font-weight: 500; color: var(--brand-green); line-height: 1.1; letter-spacing: 0.2px; }
  .contact__role { font-size: 15px; line-height: 1.2; margin-top: 2px; letter-spacing: 0.5px; }
  .contact__address { font-size: 14.5px; line-height: 18.5px; margin-top: 10px; letter-spacing: 0.6px; }
  .contact__list { list-style: none; margin-top: 8px; font-size: 15px; line-height: 19.5px; letter-spacing: 0.6px; }
  .contact__list li { display: flex; align-items: center; }
  .contact__icon { width: 10px; height: 10px; margin-right: 14px; flex: none; }

  .accent { color: var(--brand-green); }
  .web--back { position: absolute; left: 0; right: 0; top: 296px; text-align: center; font-size: 15px; color: var(--text-white); letter-spacing: 0.8px; }
</style>
</head>
<body>
<main class="canvas">
  <section class="card card--front" aria-label="Card front">
    <div class="brand"><span class="brand__dot"></span><span class="brand__name">Plavex</span></div>
    <div class="divider"></div>
    <div class="contact">
      <p class="contact__name">Harriet Dunmore</p>
      <p class="contact__role">Founder</p>
      <p class="contact__address">Brackwell House<br>QB9 3KX Partridge Way</p>
      <ul class="contact__list">
        <li>
          <svg class="contact__icon" viewBox="0 0 10 10" aria-hidden="true"><path d="M2 0.5 L3.6 0.5 L4.2 3 L3 3.8 Q4 6.2 6.2 7 L7 5.8 L9.5 6.4 L9.5 8 Q9.5 9.5 8 9.5 Q1 8.5 0.5 2 Q0.5 0.5 2 0.5Z" fill="var(--brand-green)"/></svg>
          01632 960418
        </li>
        <li>
          <svg class="contact__icon" viewBox="0 0 10 10" aria-hidden="true"><rect x="0.8" y="2" width="8.4" height="6" fill="none" stroke="var(--brand-green)" stroke-width="1"/><path d="M0.8 2 L5 5.4 L9.2 2" fill="none" stroke="var(--brand-green)" stroke-width="1"/></svg>
          harriet@plavex.co.uk
        </li>
        <li>
          <svg class="contact__icon" viewBox="0 0 10 10" aria-hidden="true"><g fill="none" stroke="var(--brand-green)" stroke-width="0.8"><circle cx="5" cy="5" r="4.3"/><ellipse cx="5" cy="5" rx="1.8" ry="4.3"/><line x1="0.7" y1="5" x2="9.3" y2="5"/></g></svg>
          www.<span class="accent">plavex</span>.co.uk
        </li>
      </ul>
    </div>
  </section>

  <section class="card card--back" aria-label="Card back">
    <div class="brand"><span class="brand__dot"></span><span class="brand__name">Plavex</span></div>
    <p class="web--back">www.<span class="accent">plavex</span>.co.uk</p>
  </section>
</main>
</body>
</html>
```